Construction company business card

One side to be the logo with the company name, The other side I would like: (Tomas verbick) Project manager 41 barrow crescent hallam 52917306224783(03) 9703 2428Info@gudeljgroup.comAnd then maybe a couple dot points saying what we do:Construction (commercial & industrial) Civil construction

Anything else please contact me!
Maybe curved st one edge of the card

Target Market(s)

Older clientele

Industry/Entity Type

Construction Company

Contact Information for Business Card

Read above

Colors
3277b5
1b1b1b
9d9d9d

Requirements
Must have
• Use my logo on one side
Nice to have
• Read above
Should not have
• Read above

```html
<!DOCTYPE html>
<html lang="en">
<head>
<meta charset="utf-8">
<title>Stonereach Property Group – Business Card</title>
<link rel="stylesheet" href="https://fonts.googleapis.com/css2?family=Roboto:wght@400;500;700;900&display=swap">
<style>
  :root {
    --brand-blue: #3277b5;
    --band-blue: #2f5f94;
    --ink: #1b1b1b;
    --grey: #9d9d9d;
    --band-grey: #c4c4c4;
    --card: #f1f1f1;
    --backdrop: #b9b9b9;
    --white: #ffffff;
    --icon: #6f6f6f;
  }
  * { box-sizing: border-box; margin: 0; padding: 0; }
  html, body {
    width: 1200px; height: 576px; overflow: hidden;
    background: var(--backdrop);
    font-family: "Roboto", Arial, sans-serif;
    color: var(--ink);
  }
  .canvas { position: relative; width: 1200px; height: 576px; }

  .card {
    position: absolute; top: 138px;
    width: 484px; height: 294px;
    background: linear-gradient(135deg, #f6f6f6, var(--card) 60%, #e9e9e9);
    border-radius: 0 22px 0 10px;
    overflow: hidden;
    box-shadow: 0 3px 8px rgba(0,0,0,.18);
  }
  .card--front { left: 82px; }
  .card--back { left: 602px; width: 482px; }

  /* Front */
  .brand-mark {
    position: absolute; left: 50%; top: 32px;
    width: 120px; height: 120px; margin-left: -60px;
    border-radius: 50%; background: var(--brand-blue);
  }
  .brand-name, .brand-sub {
    position: absolute; left: 0; width: 100%; text-align: center;
    color: var(--brand-blue); font-weight: 900; white-space: nowrap;
  }
  .brand-name { top: 162px; font-size: 38px; line-height: 40px; letter-spacing: .5px; }
  .brand-sub { top: 198px; font-size: 13px; line-height: 15px; letter-spacing: 5.6px; padding-left: 5px; }

  .website {
    position: absolute; top: 235px; left: 0; width: 100%;
    display: flex; align-items: center; justify-content: center; gap: 10px;
    font-size: 12.5px; line-height: 16px;
  }
  .website::before, .website::after {
    content: ""; width: 36px; height: 2px; background: var(--grey);
  }
  .services {
    position: absolute; top: 256px; left: 0; width: 100%;
    text-align: center; font-size: 13px; line-height: 16px;
  }
  .front-band {
    position: absolute; left: 0; bottom: 0; width: 100%; height: 14px;
    display: flex;
  }
  .front-band__grey { flex: 1; background: var(--band-grey); }
  .front-band__blue { flex: 1; background: var(--band-blue); }

  /* Back */
  .brand-row {
    position: absolute; left: 30px; top: 32px;
    display: flex; align-items: center; gap: 20px;
  }
  .brand-row__mark {
    width: 84px; height: 84px; border-radius: 50%; background: var(--brand-blue);
  }
  .brand-row__text { color: var(--brand-blue); font-weight: 900; white-space: nowrap; }
  .brand-row__name { font-size: 40px; line-height: 40px; letter-spacing: 1px; }
  .brand-row__sub { font-size: 14px; line-height: 16px; letter-spacing: 7px; margin-top: 2px; }

  .person { position: absolute; left: 30px; top: 176px; }
  .person__name { color: var(--band-blue); font-size: 18px; line-height: 22px; font-weight: 700; }
  .person__role { font-size: 13px; line-height: 16px; margin-top: 4px; }

  .contact { position: absolute; left: 282px; top: 158px; list-style: none; }
  .contact__item {
    display: flex; align-items: center; gap: 10px;
    font-size: 13px; line-height: 18px;
  }
  .contact__item svg { width: 12px; height: 12px; fill: var(--icon); }
  .contact__address {
    position: absolute; left: 282px; top: 220px; font-size: 13px; line-height: 18px;
  }
  .back-band__grey-edge {
    position: absolute; left: 0; bottom: 0; width: 130px; height: 10px; background: var(--band-grey);
  }
  .back-band__blue {
    position: absolute; right: 0; bottom: 0; width: 364px; height: 38px;
    background: var(--band-blue);
    clip-path: polygon(4% 0, 100% 0, 100% 100%, 0 100%);
    border-top-left-radius: 10px;
    color: var(--white); font-size: 12.5px; line-height: 16px;
    display: flex; align-items: center; justify-content: center; padding-left: 18px;
  }
</style>
</head>
<body>
<main class="canvas">

  <section class="card card--front" aria-label="Business card front">
    <span class="brand-mark" aria-hidden="true"></span>
    <p class="brand-name">STONEREACH</p>
    <p class="brand-sub">PROPERTY GROUP</p>
    <p class="website">www.stonereachproperty.com</p>
    <p class="services">Construction (Commercial &amp; Industrial) Civil Construction</p>
    <div class="front-band" aria-hidden="true">
      <span class="front-band__grey"></span>
      <span class="front-band__blue"></span>
    </div>
  </section>

  <section class="card card--back" aria-label="Business card back">
    <div class="brand-row">
      <span class="brand-row__mark" aria-hidden="true"></span>
      <div class="brand-row__text">
        <p class="brand-row__name">STONEREACH</p>
        <p class="brand-row__sub">PROPERTY GROUP</p>
      </div>
    </div>

    <div class="person">
      <p class="person__name">Tomas Verbick</p>
      <p class="person__role">Project Manager</p>
    </div>

    <ul class="contact">
      <li class="contact__item">
        <svg viewBox="0 0 12 12" aria-hidden="true"><path d="M1 4c0-2 2-3 5-3s5 1 5 3l-2 1-1-2H4L3 5zM3 6h6l1 5H2z"/></svg>
        (73) 0622 4783
      </li>
      <li class="contact__item">
        <svg viewBox="0 0 12 12" aria-hidden="true"><path d="M1 3h10v7H1zM1.5 3.5 6 7l4.5-3.5" stroke="#f1f1f1" stroke-width="1"/></svg>
        (03) 9418 6573
      </li>
      <li class="contact__item">
        <svg viewBox="0 0 12 12" aria-hidden="true"><circle cx="6" cy="6" r="5"/><path d="M1 6h10M6 1c-2 3-2 7 0 10M6 1c2 3 2 7 0 10" stroke="#f1f1f1" stroke-width=".8" fill="none"/></svg>
        info@verbickgroup.com
      </li>
    </ul>
    <p class="contact__address">41 Barrow Crescent Kerrivale 5291</p>

    <span class="back-band__grey-edge" aria-hidden="true"></span>
    <div class="back-band__blue">Construction (Commercial &amp; Industrial) Civil Construction</div>
  </section>

</main>
</body>
</html>
```